Unternehmen für Ordnung und Sauberkeit am Arbeitsplatz und Produkte zur Produktionsoptimierung benötigt Visitenkarten und Briefpapier
Zielgruppe
Produkte für Ordnung und Sauberkeit am Arbeitsplatz, Organisation von Arbeitsplätzen, Produkte zur Vereinfachung von Arbeitsabläufen, Produkte zur Produktionsoptimierung unter dem Lean Gedanke, Schlagwort: "5S", nachhaltig, sauber
Aufgabenstellung
Wir sind auf der Suche nach Visitenkarten und Briefpapier für das Unternehmen yourTidor. Nachhaltig, Sauber usw.. Unser Firmenlogo finden Sie anbei.

```html
<!DOCTYPE html>
<html lang="de">
<head>
<meta charset="utf-8">
<title>yourTidor – Geschäftsausstattung</title>
<link href="https://fonts.googleapis.com/css2?family=Source+Sans+3:ital,wght@0,300;0,400;0,600;0,700;1,700&display=swap" rel="stylesheet">
<style>
:root{
  --green:#1e8f3e;
  --green-light:#8cc79a;
  --ink:#444;
  --gray:#5e5e5e;
  --paper:#fff;
  --edge:#c9c9c9;
  --shadow:rgba(0,0,0,.28);
}
*{margin:0;padding:0;box-sizing:border-box}
html,body{width:848px;height:1200px;overflow:hidden;background:#fff}
body{position:relative;font-family:"Source Sans 3",sans-serif;color:var(--ink)}
.sheet{position:absolute;background:var(--paper);border:1px solid var(--edge);box-shadow:3px 4px 5px var(--shadow)}
.abs{position:absolute}
.brand{display:flex;align-items:center;white-space:nowrap}
.brand-mark{background:var(--green);flex:none}
.brand-name{font-weight:700;color:var(--gray);line-height:1}
.tagline{display:flex;font-weight:700;font-style:italic;color:var(--gray);white-space:nowrap}
.g{color:var(--green)}
.b{font-weight:700}
.fold{position:absolute;left:0;width:8px;height:.6px;background:var(--green)}
.fold.mid{width:10px;height:1px}
.rule{position:absolute;height:.6px;background:var(--green-light)}

/* hero */
.hero{left:314px;top:112px}
.hero .brand-mark{width:58px;height:58px;margin-right:10px}
.hero .brand-name{font-size:38px}

/* cards */
.card{width:170px;height:110px}
.card .front-brand{left:0;right:0;top:30px;justify-content:center}
.card .front-brand .brand-mark{width:24px;height:24px;margin-right:5px}
.card .front-brand .brand-name{font-size:17px}
.card .tagline{left:0;right:0;top:81px;justify-content:center;gap:11px;font-size:6px}
.card-contact .brand{left:16px;top:45px}
.card-contact .brand-mark{width:15px;height:15px;margin-right:3px}
.card-contact .brand-name{font-size:10.5px}
.card-contact .info{left:84px;top:34px;font-size:4.6px;line-height:6.2px}
.card-contact .info dl{display:grid;grid-template-columns:25px auto;margin-top:2.5px}
.card-contact .info dt{font-weight:700}
.card-contact .info dd{color:var(--green)}
.card-centered .brand{left:0;right:0;top:40px;justify-content:center}
.card-centered .brand-mark{width:17px;height:17px;margin-right:4px}
.card-centered .brand-name{font-size:12px}
.card-centered .info{left:0;right:0;top:88px;text-align:center;font-size:4.3px;line-height:6.2px;font-weight:600}

/* large letter */
.letter-lg{left:50px;top:550px;width:417px;height:589px}
.letter-lg .top-brand{left:0;right:0;top:18px;justify-content:center}
.letter-lg .top-brand .brand-mark{width:38px;height:38px;margin-right:6px}
.letter-lg .top-brand .brand-name{font-size:25px}
.letter-lg .tagline{left:0;right:0;top:70px;justify-content:center;gap:12px;font-size:6.3px}
.letter-lg .sender{left:40px;top:119px;font-size:6.1px}
.letter-lg .recipient{left:40px;top:135px;font-size:6.8px;line-height:9.2px}
.letter-lg .contact{left:345px;top:119px;font-size:4.6px;line-height:6px;font-weight:600}
.letter-lg .contact dl{display:grid;grid-template-columns:12px auto}
.letter-lg .contact dt{color:var(--green);font-weight:700}
.letter-lg .date{right:25px;top:197px;font-size:6.8px;font-weight:700;color:var(--green)}
.letter-lg .body{left:40px;top:245px;width:240px;font-size:6.6px;line-height:10.5px;font-weight:300;text-align:justify}
.letter-lg .body p{margin-bottom:10.5px}
.letter-lg .closing{left:40px;top:466px;font-size:6.6px;font-weight:300}
.letter-lg .rule{left:40px;width:344px;top:550px}
.letter-lg .footer{left:0;right:0;top:556px;text-align:center;font-size:5.2px;line-height:7.9px;font-weight:600}

/* small letters */
.letter-sm{left:486px;width:296px;height:418px}
.letter-sm .head{left:28px;top:10px;font-size:4.8px}
.letter-sm .table{font-size:3.9px;line-height:7.3px;display:grid}
.letter-sm .table dt{font-weight:700}
.letter-sm .table dd{color:var(--green)}
.letter-sm .t-contact{grid-template-columns:23px 50px}
.letter-sm .t-bank{grid-template-columns:22px auto}
.letter-sm .bank-title{font-size:3.9px;font-weight:700;line-height:7.3px}
.letter-sm .side-brand{right:22px;top:10px}
.letter-sm .side-brand .brand-mark{width:22px;height:22px;margin-right:4px}
.letter-sm .side-brand .brand-name{font-size:14.5px}
.letter-sm .tagline{right:17px;top:49px;gap:8px;font-size:4.2px}
.letter-sm .sender{left:28px;top:84px;font-size:3.9px}
.letter-sm .recipient{left:28px;top:97px;font-size:4.5px;line-height:6.4px}
.letter-sm .date{right:18px;top:141px;font-size:4.5px;font-weight:700;color:var(--gray)}
.letter-sm .body{left:28px;top:157px;width:170px;font-size:4.3px;line-height:7.45px;font-weight:300;text-align:justify}
.letter-sm .body p{margin-bottom:7.45px}
.letter-sm .closing{left:28px;top:313px;font-size:4.3px;font-weight:300}
</style>
</head>
<body>

<!-- brand hero -->
<div class="abs brand hero"><span class="brand-mark"></span><span class="brand-name">yourTidor</span></div>

<!-- business card: front -->
<section class="sheet card" style="left:50px;top:293px">
  <div class="abs brand front-brand"><span class="brand-mark"></span><span class="brand-name">yourTidor</span></div>
  <div class="abs tagline"><span>Ordnung</span><span>Sauberkeit</span><span>Organisation</span></div>
</section>
<section class="sheet card" style="left:298px;top:293px">
  <div class="abs brand front-brand"><span class="brand-mark"></span><span class="brand-name">yourTidor</span></div>
  <div class="abs tagline"><span>Ordnung</span><span>Sauberkeit</span><span>Organisation</span></div>
</section>

<!-- business card: back, contact -->
<section class="sheet card card-contact" style="left:50px;top:414px">
  <div class="abs brand"><span class="brand-mark"></span><span class="brand-name">yourTidor</span></div>
  <div class="abs info">
    <div class="b">Mister XY</div>
    <div class="g">Musterstraße 1</div>
    <div class="g">12345 Musterstadt</div>
    <dl><dt>T</dt><dd>0123 // 456 789</dd><dt>F</dt><dd>098 // 765 43 21</dd><dt>M</dt><dd>info@yourtidor.de</dd><dt>W</dt><dd>www.yourtidor.de</dd></dl>
  </div>
</section>

<!-- business card: back, centered -->
<section class="sheet card card-centered" style="left:298px;top:414px">
  <div class="abs brand"><span class="brand-mark"></span><span class="brand-name">yourTidor</span></div>
  <div class="abs info">
    <div><span class="g b">yourTidor</span> | Musterstraße 1 | 12345 Musterstadt</div>
    <div><span class="g">T</span> 0123 45 67 89 | <span class="g">F</span> 0987 65 43 21</div>
    <div><span class="g">M</span> info@yourtidor.de | <span class="g">W</span> www.yourtidor.de</div>
  </div>
</section>

<!-- letterhead: centered variant -->
<section class="sheet letter-lg">
  <div class="abs brand top-brand"><span class="brand-mark"></span><span class="brand-name">yourTidor</span></div>
  <div class="abs tagline"><span>Ordnung</span><span>Sauberkeit</span><span>Organisation</span></div>
  <div class="abs sender"><span class="b">yourTidor</span> <span class="g">| Musterstraße 1 | 12345 Musterstadt</span></div>
  <div class="abs recipient">Klara Klärchen<br>Klärchenstraße 1<br><br>12345 Klärchenstadt</div>
  <div class="abs contact">
    <div class="g b">KONTAKT</div>
    <dl><dt>T</dt><dd>1234 &nbsp; 56 &nbsp; 78 &nbsp; 90</dd><dt>F</dt><dd>0987 &nbsp; 65 &nbsp; 43 &nbsp; 21</dd><dt>M</dt><dd>&nbsp; info@yourtidor.de</dd><dt>W</dt><dd>&nbsp; www.yourtidor.de</dd></dl>
  </div>
  <div class="abs date">Musterstadt, den 08. Mai 2014</div>
  <div class="abs body">
    <p>Sehr geehrte Damen und Herren,</p>
    <p>Quia quasite delenient, occus eum reius volenec erspitia conet od mo cor am et fugiate nimagnihil iume pratem aut facest ium, utet doluptat. Am repudae plisquostiis consecae. Odi reriam que ditae por apedis aliam is sint aspero berae si sin nonsequis int magnam sunt, ommoluptae. Osapel in conet ut diae.</p>
    <p>Obit, sim essim quo vendae sunto ipsam re experior anditas et earum is ducius aciaepu daestestem re prae. Untia desto offici veratibustis est moloribus aped que natibusae dolut litate culpa sa que imus, occae se etur? Tibus, quis esequis dolestios minientint. Ut et modipsandus, te seque prehenim non reptur assequid ut hic to esequunt veliquunt, quibeat abo. Officius.</p>
    <p>Temposam quat acessit atioribus dolore quati quiaspiciet denis molupta turerfe rferovit faccum facepelitium ipicto blameturenis arciamus, conest doluptate ommost et dolorio nsenimo luptate volo ommodis velicid quiae dolorec torenis nossum volorion cum et ea qui rate perenim non cullaccum quatest, nimaioresto molupta quae re cum voluptation corem ut qui aut eum apit lam qui oditatur ad ulparchicto velene voluptat et ute dolupta voluptaerati ime lacea aliatenias dit lab ipsunt.</p>
  </div>
  <div class="abs closing">Mit freundlichen Grüßen</div>
  <span class="fold" style="top:479px"></span>
  <span class="fold" style="top:195px"></span>
  <span class="fold mid" style="top:280px"></span>
  <span class="fold" style="top:403px"></span>
  <div class="rule"></div>
  <div class="abs footer">
    <div><span class="g b">yourTidor</span> | Musterstraße 1 | 12345 Musterstadt</div>
    <div>Geschäftsführung <span class="g b">MisterXY</span> | Amtsgericht <span class="g b">XY</span> | Steuernummer <span class="g b">123/4567/8900</span> &nbsp;| USt.- ID <span class="g b">DE XXXXXXX</span></div>
    <div><span class="g b">BANK</span> Musterbank Muster | <span class="g b">IBAN</span> DE 1234 5678 9098 7654 321| <span class="g b">BIC</span> MUSTER XX</div>
  </div>
</section>

<!-- letterhead: header variant -->
<section class="sheet letter-sm" style="top:293px">
  <div class="abs head"><span class="b">yourTidor</span> <span class="g">| Musterstraße 1 | 12345 Musterstadt</span></div>
  <dl class="abs table t-contact" style="left:28px;top:24px"><dt>T</dt><dd>0123 // 456 789</dd><dt>F</dt><dd>098 // 765 43 21</dd><dt>M</dt><dd>info@yourtidor.de</dd><dt>W</dt><dd>www.yourtidor.de</dd></dl>
  <div class="abs" style="left:103px;top:24px">
    <div class="bank-title">Musterbank Muster</div>
    <dl class="table t-bank"><dt>IBAN</dt><dd>DE 1234 5678 9098 7654 321</dd><dt>BIC</dt><dd>MUSTERXX</dd><dt>USt.-IdNr.</dt><dd>123 456 789 0</dd></dl>
  </div>
  <div class="abs brand side-brand"><span class="brand-mark"></span><span class="brand-name">yourTidor</span></div>
  <div class="abs tagline"><span>Ordnung</span><span>Sauberkeit</span><span>Organisation</span></div>
  <div class="rule" style="left:28px;width:250px;top:57px"></div>
  <div class="abs sender"><span class="b">yourTidor</span> <span class="g">| Musterstraße 1 | 12345 Musterstadt</span></div>
  <div class="abs recipient">Klara Klärchen<br>Klärchenstraße 1<br><br>12345 Klärchenstadt</div>
  <div class="abs date">Musterstadt, den 08. Mai 2014</div>
  <div class="abs body">
    <p>Sehr geehrte Damen und Herren,</p>
    <p>Quia quasite delenient, occus eum reius volenec erspitia conet od mo cor am et fugiate nimagnihil iume pratem aut facest ium, utet doluptat. Am repudae plisquostiis consecae. Odi reriam que ditae por apedis aliam is sint aspero berae si sin nonsequis int magnam sunt, ommoluptae. Osapel in conet ut diae.</p>
    <p>Obit, sim essim quo vendae sunto ipsam re experior anditas et earum is ducius aciaepu daestestem re prae. Untia desto offici veratibustis est moloribus aped que natibusae dolut litate culpa sa que imus, occae se etur? Tibus, quis esequis dolestios minientint. Ut et modipsandus, te seque prehenim non reptur assequid ut hic to esequunt veliquunt, quibeat abo. Officius.</p>
    <p>Temposam quat acessit atioribus dolore quati quiaspiciet denis molupta turerfe rferovit faccum facepelitium ipicto blameturenis arciamus, conest doluptate ommost et dolorio nsenimo luptate volo ommodis velicid quiae dolorec torenis nossum volorion cum et ea qui rate perenim non cullaccum quatest, nimaioresto molupta quae re cum voluptation corem ut qui aut eum apit lam qui oditatur ad ulparchicto velene voluptat et ute dolupta voluptaerati ime lacea aliatenias dit lab ipsunt.</p>
  </div>
  <div class="abs closing">Mit freundlichen Grüßen</div>
  <span class="fold" style="top:148px"></span>
  <span class="fold mid" style="top:208px"></span>
  <span class="fold" style="top:295px"></span>
</section>

<!-- letterhead: footer variant -->
<section class="sheet letter-sm" style="top:721px">
  <div class="abs brand side-brand"><span class="brand-mark"></span><span class="brand-name">yourTidor</span></div>
  <div class="abs tagline"><span>Ordnung</span><span>Sauberkeit</span><span>Organisation</span></div>
  <div class="abs sender"><span class="b">yourTidor</span> <span class="g">| Musterstraße 1 | 12345 Musterstadt</span></div>
  <div class="abs recipient">Klara Klärchen<br>Klärchenstraße 1<br><br>12345 Klärchenstadt</div>
  <div class="abs date">Musterstadt, den 08. Mai 2014</div>
  <div class="abs body">
    <p>Sehr geehrte Damen und Herren,</p>
    <p>Quia quasite delenient, occus eum reius volenec erspitia conet od mo cor am et fugiate nimagnihil iume pratem aut facest ium, utet doluptat. Am repudae plisquostiis consecae. Odi reriam que ditae por apedis aliam is sint aspero berae si sin nonsequis int magnam sunt, ommoluptae. Osapel in conet ut diae.</p>
    <p>Obit, sim essim quo vendae sunto ipsam re experior anditas et earum is ducius aciaepu daestestem re prae. Untia desto offici veratibustis est moloribus aped que natibusae dolut litate culpa sa que imus, occae se etur? Tibus, quis esequis dolestios minientint. Ut et modipsandus, te seque prehenim non reptur assequid ut hic to esequunt veliquunt, quibeat abo. Officius.</p>
    <p>Temposam quat acessit atioribus dolore quati quiaspiciet denis molupta turerfe rferovit faccum facepelitium ipicto blameturenis arciamus, conest doluptate ommost et dolorio nsenimo luptate volo ommodis velicid quiae dolorec torenis nossum volorion cum et ea qui rate perenim non cullaccum quatest, nimaioresto molupta quae re cum voluptation corem ut qui aut eum apit lam qui oditatur ad ulparchicto velene voluptat et ute dolupta voluptaerati ime lacea aliatenias dit lab ipsunt.</p>
  </div>
  <div class="abs closing">Mit freundlichen Grüßen</div>
  <span class="fold" style="top:148px"></span>
  <span class="fold mid" style="top:208px"></span>
  <span class="fold" style="top:295px"></span>
  <div class="rule" style="left:28px;width:246px;top:372px"></div>
  <div class="abs" style="left:0;right:0;top:375px;text-align:center;font-size:4.8px"><span class="b">yourTidor</span> <span class="g">| Musterstraße 1 | 12345 Musterstadt</span></div>
  <dl class="abs table t-contact" style="left:36px;top:384px"><dt>T</dt><dd>0123 // 456 789</dd><dt>F</dt><dd>098 // 765 43 21</dd><dt>M</dt><dd>info@yourtidor.de</dd><dt>W</dt><dd>www.yourtidor.de</dd></dl>
  <div class="abs" style="left:180px;top:384px">
    <div class="bank-title">Musterbank Muster</div>
    <dl class="table t-bank"><dt>IBAN</dt><dd>DE 1234 5678 9098 7654 321</dd><dt>BIC</dt><dd>MUSTERXX</dd><dt>USt.-IdNr.</dt><dd>123 456 789 0</dd></dl>
  </div>
</section>

</body>
</html>
```